business card for a massage therapy practice named 'Cedar and Willow Massage Studio'

I really need a trendy, yet easy on the eyes business card to complement my logo. Ideally with some gold or rose gold foil work.

My uploaded file of the logo I have in horizontal but I have a vertical version as well. Another color that is used in the website is a blush pink here and there. I'd like to see some trendy tropical leaves in the design.

```html
<!DOCTYPE html>
<html lang="en">
<head>
<meta charset="utf-8">
<title>Cedar and Willow Massage Studio – Business Card</title>
<link href="https://fonts.googleapis.com/css2?family=Open+Sans:wght@400;600&display=swap" rel="stylesheet">
<style>
  :root {
    --stage: #2e2e30;
    --card-black: #050505;
    --card-white: #ffffff;
    --ink: #1c1c1c;
    --mint: #5fcfae;
    --gold-deep: #8f7d52;
    --gold: #a08e62;
    --gold-light: #c4b48a;
    --white: #ffffff;
  }
  * { box-sizing: border-box; margin: 0; padding: 0; }
  html, body {
    width: 1200px; height: 782px; overflow: hidden;
    background: var(--stage);
    font-family: "Open Sans", Arial, sans-serif;
  }
  .canvas { position: relative; width: 1200px; height: 782px; }
  .card {
    position: absolute; width: 560px; height: 320px;
    box-shadow: 0 10px 30px rgba(0,0,0,0.45);
    overflow: hidden;
  }

  /* Back side */
  .card--back { left: 560px; top: 80px; background: var(--card-black); }
  .card--back .brand {
    position: absolute; left: 0; right: 0; top: 124px;
    display: flex; align-items: center; justify-content: center; gap: 16px;
  }
  .brand__mark {
    width: 34px; height: 34px; border-radius: 50%;
    background: var(--gold); flex: none;
  }
  .card--back .brand__name {
    color: var(--white); font-weight: 600; font-size: 27px; line-height: 1.15;
    letter-spacing: 0.5px;
  }

  /* Front side */
  .card--front { left: 90px; top: 380px; background: var(--card-white); }
  .card--front .brand { position: absolute; left: 34px; top: 28px; }
  .card--front .brand__name {
    color: var(--ink); font-weight: 600; font-size: 25px; line-height: 1.18;
  }
  .contact { position: absolute; left: 34px; top: 124px; color: var(--ink); }
  .contact__name {
    color: var(--mint); font-size: 17px; letter-spacing: 1px;
    text-transform: uppercase; margin-bottom: 2px;
  }
  .contact__role { font-size: 14px; line-height: 1.45; margin-bottom: 6px; }
  .contact__line {
    font-size: 14px; line-height: 1.45;
    display: flex; align-items: center; gap: 7px;
  }
  .contact__icon { width: 13px; height: 13px; flex: none; }

  .feature-art {
    position: absolute; right: 40px; top: 24px; width: 200px; height: 272px;
    border-radius: 6px;
    background: linear-gradient(160deg, var(--gold-light) 0%, var(--gold) 45%, var(--gold-deep) 100%);
  }
</style>
</head>
<body>
<main class="canvas">

  <section class="card card--back" aria-label="Card back">
    <div class="brand">
      <span class="brand__mark" aria-hidden="true"></span>
      <p class="brand__name">Cedar and Willow<br>Massage Studio</p>
    </div>
  </section>

  <section class="card card--front" aria-label="Card front">
    <div class="brand">
      <p class="brand__name">Cedar and Willow<br>Massage Studio</p>
    </div>

    <div class="contact">
      <p class="contact__name">Marisa Delgado</p>
      <p class="contact__role">Massage Therapist</p>
      <p class="contact__line">418 Laurel Ave. suite 210</p>
      <p class="contact__line">Fresno, CA 93721</p>
      <p class="contact__line">
        <svg class="contact__icon" viewBox="0 0 16 16" aria-hidden="true">
          <rect x="0" y="0" width="16" height="16" rx="2" fill="#5fcfae"/>
          <path d="M4 5c0-1 1-1.5 2-1.5l1 2-1 1c.6 1.3 1.5 2.2 2.8 2.8l1-1 2 1c0 1-.5 2-1.5 2C6.5 11.3 4 8.8 4 5z" fill="#fff"/>
        </svg>
        (559) 555-0148
      </p>
      <p class="contact__line">
        <svg class="contact__icon" viewBox="0 0 16 16" aria-hidden="true">
          <rect x="0" y="2" width="16" height="12" rx="1.5" fill="#5fcfae"/>
          <path d="M1.5 3.5 8 9l6.5-5.5" fill="none" stroke="#fff" stroke-width="1.4"/>
        </svg>
        cedarandwillow@mail.com
      </p>
    </div>

    <div class="feature-art" role="img" aria-label="Large gold foil tropical illustration"></div>
  </section>

</main>
</body>
</html>
```